KLV Plant Services

We are a heavy diesel mechanical business with additional air con certificates, remapping engine rebuilt

Contact Information for Business Card

Company Name, Director Name, Managing Director, Contact details, email and website

Font styles to use
Serif
Script

```html
<!DOCTYPE html>
<html lang="en">
<head>
<meta charset="UTF-8">
<title>KLV Plant Services – Business Card</title>
<link href="https://fonts.googleapis.com/css2?family=Poppins:wght@400;700&display=swap" rel="stylesheet">
<style>
  :root {
    --navy: #0d0f86;
    --ink: #111111;
    --paper: #ffffff;
    --paper-shade: #e9e9ec;
    --backdrop: #3a3a3d;
  }
  * { margin: 0; padding: 0; box-sizing: border-box; }
  html, body { width: 1200px; height: 900px; overflow: hidden; }
  body {
    background: var(--backdrop);
    font-family: 'Poppins', sans-serif;
    position: relative;
  }
  .card {
    position: absolute;
    left: 267px;
    width: 665px;
    height: 380px;
    overflow: hidden;
    box-shadow: 0 14px 30px rgba(0,0,0,0.45);
  }
  .card-front { top: 50px; background: linear-gradient(135deg, var(--paper) 40%, var(--paper-shade)); }
  .card-back { top: 470px; background: var(--navy); }
  .wave { position: absolute; inset: 0; }
  .brand {
    position: absolute;
    display: flex;
    align-items: center;
    gap: 12px;
    font-weight: 700;
    color: var(--navy);
  }
  .card-front .brand { left: 48px; top: 34px; font-size: 26px; }
  .brand-dot {
    width: 34px; height: 34px;
    border-radius: 50%;
    background: var(--navy);
    flex: none;
  }
  .card-back .brand {
    left: 0; right: 0; top: 0; bottom: 0;
    justify-content: center;
    color: var(--paper);
    font-size: 46px;
  }
  .card-back .brand-dot { width: 56px; height: 56px; background: var(--paper); }
  .person {
    position: absolute;
    right: 48px;
    top: 100px;
    text-align: right;
  }
  .person-name {
    font-weight: 700;
    font-size: 27px;
    color: var(--navy);
    letter-spacing: 0.5px;
  }
  .person-role { font-size: 15px; color: var(--ink); }
  .contact {
    position: absolute;
    right: 140px;
    top: 256px;
    text-align: right;
    color: var(--paper);
    font-size: 13.5px;
    line-height: 1.42;
    list-style: none;
  }
  .contact li { display: flex; justify-content: flex-end; align-items: center; gap: 7px; }
  .contact svg { width: 13px; height: 13px; flex: none; }
  .contact .address { margin-bottom: 5px; }
</style>
</head>
<body>

<section class="card card-front">
  <svg class="wave" viewBox="0 0 665 380" preserveAspectRatio="none" aria-hidden="true">
    <path d="M0,110 C140,250 330,190 470,215 C560,232 590,300 610,380 L0,380 Z" fill="var(--navy)"/>
    <path d="M0,90 C140,232 340,172 485,197 C578,213 610,290 632,380" fill="none" stroke="var(--ink)" stroke-width="7"/>
    <path d="M0,76 C140,218 350,158 498,182 C592,198 628,280 652,380" fill="none" stroke="var(--navy)" stroke-width="4"/>
  </svg>

  <div class="brand">
    <span class="brand-dot"></span>
    <span>KLV Plant Services</span>
  </div>

  <div class="person">
    <div class="person-name">MARK ELLISON</div>
    <div class="person-role">Director</div>
  </div>

  <ul class="contact">
    <li class="address">1820 Harlow Rd Millbrook<br>Falls, GA 30112</li>
    <li>470-555-0148
      <svg viewBox="0 0 24 24"><path fill="currentColor" d="M6.6 10.8a15 15 0 0 0 6.6 6.6l2.2-2.2a1 1 0 0 1 1-.25 11.4 11.4 0 0 0 3.6.57 1 1 0 0 1 1 1V20a1 1 0 0 1-1 1A17 17 0 0 1 3 4a1 1 0 0 1 1-1h3.5a1 1 0 0 1 1 1c0 1.25.2 2.45.57 3.57a1 1 0 0 1-.25 1z"/></svg>
    </li>
    <li>info@klvplantservices.com
      <svg viewBox="0 0 24 24"><rect x="2" y="5" width="20" height="14" fill="none" stroke="currentColor" stroke-width="2"/><path d="M2 6l10 7 10-7" fill="none" stroke="currentColor" stroke-width="2"/></svg>
    </li>
    <li>www.klvplantservices.com
      <svg viewBox="0 0 24 24"><circle cx="12" cy="12" r="10" fill="none" stroke="currentColor" stroke-width="2"/><path d="M2 12h20M12 2c3 3 3 17 0 20M12 2c-3 3-3 17 0 20" fill="none" stroke="currentColor" stroke-width="1.6"/></svg>
    </li>
  </ul>
</section>

<section class="card card-back">
  <div class="brand">
    <span class="brand-dot"></span>
    <span>KLV Plant Services</span>
  </div>
</section>

</body>
</html>
```